Small corporate website template design

I need a couple templates designed for a small corporate website. The corporate site reflects the existence of the parent company which will own various brands/services that have their own websites, so it will mainly be used to present who we are, what we do, what is happening (news/events), how to contact us, link off to our other brand/service sites, as well as post information for public relations, investors, and job opportunities.

The company name is Brelvanto LLC (www.brelvanto-example.com), and the name is representative of stratified layers of interconnected digital services. The corporate site is not expected to generate a bunch of fanfare - that honor will be reserved for the externally linked brand/service sites.

The provided logo may be manipulated in color, size, shape, positioning, etc. to get it to fit with the design, but should be integrated in some way.

What we are looking for is a home page layout as well as a template for an inner page whereby the navigation/logo, etc may be diminished to some extent for the inner pages. We are also interested in reusable elements such as dividers, content containers, etc. in order to represent the types of information described above that we would like to present as described above.

We are particularly interested in consistency of design elements, conservative use of color (including consideration of accessibility concerns), judicious use of whitespace in favor of simplified messaging, and something lending itself well to internationalization/translation.

Target Market(s)

Small business owners, entrepreneurs (B2B)

Number of Pages Required

2 page

Font styles to use
Sans Serif

Requirements
Must have
• See the attached PDF with the logo concept, color swatches, and comparative sites.

```html
<!DOCTYPE html>
<html lang="en">
<head>
<meta charset="utf-8">
<title>Brelvanto — Home</title>
<link href="https://fonts.googleapis.com/css2?family=Montserrat:wght@500;600&family=Open+Sans:wght@400;600&display=swap" rel="stylesheet">
<style>
:root{
  --teal:#16816d;
  --hero-top:#1f3f7a;
  --hero-bottom:#2d5a99;
  --band:#1f2c86;
  --band-deep:#1a2470;
  --panel:#eaf0f8;
  --tab-idle:#e6edf6;
  --tab-idle-text:#a9b6c8;
  --body-text:#555b63;
  --btn-muted:#b9c8db;
  --btn-muted-text:#26344a;
  --footer:#262626;
  --footer-text:#c9c9c9;
  --social-a:#2c4f8f;
  --social-b:#2f8fd8;
  --social-c:#1f6ab5;
  --white:#ffffff;
}
*{margin:0;padding:0;box-sizing:border-box}
html,body{width:934px;height:1200px;overflow:hidden;background:var(--white)}
body{position:relative;font-family:"Open Sans",Arial,sans-serif}
.abs{position:absolute}

.hero{left:0;top:0;width:934px;height:478px;background:linear-gradient(160deg,var(--hero-top),var(--hero-bottom) 60%,#24487f)}
.brand{left:103px;top:26px;display:flex;align-items:center;gap:9px;color:var(--white);font-family:"Montserrat",sans-serif;font-weight:600;font-size:27px}
.brand-mark{width:26px;height:26px;border-radius:50%;background:var(--white)}
.nav-link{top:40px;font-size:9px;color:var(--white);white-space:nowrap}
.signin{left:776px;top:34px;width:55px;height:24px;background:var(--white);border-radius:2px;color:#555;font-size:9px;display:flex;align-items:center;justify-content:center;gap:4px}
.headline{left:0;top:200px;width:934px;text-align:center;color:var(--white);font-family:"Montserrat",sans-serif;font-weight:600;font-size:24.5px}
.hero-cta{left:414px;top:245px;width:106px;height:28px;background:var(--teal);color:var(--white);font-family:"Montserrat",sans-serif;font-size:12.5px;display:flex;align-items:center;justify-content:center}
.arrow{top:443px;width:19px;height:16px;border:1px solid rgba(255,255,255,.85)}

.tab{top:532px;height:37px;font-family:"Montserrat",sans-serif;font-weight:600;font-size:19px;display:flex;align-items:center;justify-content:center}
.tab-active{left:326px;width:139px;background:var(--teal);color:var(--white)}
.tab-idle{left:469px;width:140px;background:var(--tab-idle);color:var(--tab-idle-text)}
.about{left:103px;top:573px;width:364px;height:199px;background:var(--panel)}
.about p{position:absolute;left:23px;top:17px;width:330px;font-size:10.4px;line-height:17.4px;color:var(--body-text)}
.read-more{left:23px;top:149px;width:75px;height:27px;background:var(--btn-muted);color:var(--btn-muted-text);font-size:9.8px;border-radius:2px;display:flex;align-items:center;justify-content:center}
.about-photo{left:467px;top:573px;width:364px;height:199px;background:linear-gradient(120deg,#8a8e92,#b7a58e 45%,#3d6a86 70%,#d8dbdf)}

.band{left:0;top:835px;width:934px;height:236px;background:radial-gradient(circle at 70% 40%,#2a3fa3,var(--band) 55%,var(--band-deep))}
.hex{top:857px;width:200px;height:193px}
.hex svg.shape{position:absolute;left:0;top:0}
.hex .icon{position:absolute;left:80px;top:58px}
.hex h3{position:absolute;left:0;top:108px;width:200px;text-align:center;font-family:"Montserrat",sans-serif;font-weight:600;font-size:16.5px;color:var(--teal)}

.footer{left:0;top:1071px;width:934px;height:129px;background:var(--footer)}
.footer-links{top:30px;width:934px;text-align:center;font-size:9px;color:var(--footer-text);word-spacing:2px}
.copyright{top:50px;width:934px;text-align:center;font-size:9px;color:var(--footer-text)}
.social{top:79px;width:20px;height:20px;border-radius:50%;display:flex;align-items:center;justify-content:center}
</style>
</head>
<body>

<section class="abs hero" role="img" aria-label="Photo of a team working together at computers in a bright office, tinted blue"></section>
<div class="abs brand"><span class="brand-mark"></span>Brelvanto</div>
<nav>
  <span class="abs nav-link" style="left:466px">Who We Are</span>
  <span class="abs nav-link" style="left:539px">What We Do</span>
  <span class="abs nav-link" style="left:612px">News</span>
  <span class="abs nav-link" style="left:657px">Contact Us</span>
  <span class="abs nav-link" style="left:724px">Careers</span>
</nav>
<div class="abs signin">
  <svg width="9" height="8" viewBox="0 0 9 8"><path d="M0 3h4V1l3 3-3 3V5H0z" fill="#555"/><path d="M6 0h3v8H6" fill="none" stroke="#555" stroke-width="1.2"/></svg>Sign In
</div>
<h1 class="abs headline">Adaptive Software Technology for the Digital Revolution</h1>
<div class="abs hero-cta">CONTACT US</div>
<div class="abs arrow" style="left:446px"><svg width="17" height="14" viewBox="0 0 17 14"><path d="M10 3l-4 4 4 4" fill="none" stroke="#fff" stroke-width="1.2"/></svg></div>
<div class="abs arrow" style="left:469px"><svg width="17" height="14" viewBox="0 0 17 14"><path d="M7 3l4 4-4 4" fill="none" stroke="#fff" stroke-width="1.2"/></svg></div>

<div class="abs tab tab-active">Who We Are</div>
<div class="abs tab tab-idle">What We Do</div>
<section class="abs about">
  <p>Phasellus consequat sagittis nisi suscipit feugiat. Cras eget leo sed nunc hendrerit ultricies eu at nisl. Praesent iaculis faucibus urna sit amet lacinia. Maecenas consequat justo enim, ac mattis massa imperdiet quis. Fusce eget neque elit. Sed augue orci, elementum in magna congue, tincidunt vulputate erat. Aliquam consectetur orci molestie dictum molestie. Proin eget congue nulla, vel tempor diam. Ut non ante est.</p>
  <div class="abs read-more">READ MORE</div>
</section>
<div class="abs about-photo" role="img" aria-label="Photo of a smiling employee on the phone at an office desk"></div>

<section class="abs band" role="img" aria-label="Deep blue background with a faint network of connected points"></section>

<div class="abs hex" style="left:103px">
  <svg class="shape" width="200" height="193" viewBox="0 0 200 193"><polygon points="100,0 200,48 200,145 100,193 0,145 0,48" fill="#fff"/></svg>
  <svg class="icon" width="40" height="34" viewBox="0 0 40 34"><rect x="5" y="4" width="30" height="28" rx="2" fill="none" stroke="#16816d" stroke-width="2.5"/><rect x="5" y="4" width="30" height="7" fill="#16816d"/><rect x="11" y="0" width="3" height="7" fill="#16816d"/><rect x="26" y="0" width="3" height="7" fill="#16816d"/><g fill="#16816d"><rect x="9" y="14" width="4" height="4"/><rect x="15" y="14" width="4" height="4"/><rect x="21" y="14" width="4" height="4"/><rect x="27" y="14" width="4" height="4"/><rect x="9" y="20" width="4" height="4"/><rect x="15" y="20" width="4" height="4"/><rect x="21" y="20" width="4" height="4"/><rect x="27" y="20" width="4" height="4"/><rect x="9" y="26" width="4" height="3"/><rect x="15" y="26" width="4" height="3"/><rect x="21" y="26" width="4" height="3"/></g></svg>
  <h3>What Is Happening?</h3>
</div>
<div class="abs hex" style="left:367px">
  <svg class="shape" width="200" height="193" viewBox="0 0 200 193"><polygon points="100,0 200,48 200,145 100,193 0,145 0,48" fill="#fff"/></svg>
  <svg class="icon" width="40" height="34" viewBox="0 0 40 34"><path d="M14 7V3h12v4" fill="none" stroke="#16816d" stroke-width="3"/><rect x="2" y="7" width="36" height="25" rx="3" fill="#16816d"/><rect x="2" y="17" width="36" height="2" fill="#fff"/><rect x="17" y="15" width="6" height="6" fill="#fff"/><rect x="18.5" y="16.5" width="3" height="3" fill="#16816d"/></svg>
  <h3>Careers</h3>
</div>
<div class="abs hex" style="left:631px">
  <svg class="shape" width="200" height="193" viewBox="0 0 200 193"><polygon points="100,0 200,48 200,145 100,193 0,145 0,48" fill="#fff"/></svg>
  <svg class="icon" width="40" height="34" viewBox="0 0 40 34"><rect x="1" y="2" width="38" height="30" rx="3" fill="#16816d"/><path d="M1 7l19 12 19-12" fill="none" stroke="#fff" stroke-width="2.5"/></svg>
  <h3>Contact Us</h3>
</div>

<footer class="abs footer">
  <div class="abs footer-links">Who We Are &nbsp;|&nbsp; What We Do &nbsp;|&nbsp; News &nbsp;|&nbsp; Contact Us &nbsp;|&nbsp; Careers</div>
  <div class="abs copyright">Copyright &copy; 2108 &nbsp;Brelvanto. &nbsp;All rights reserved.</div>
  <a class="abs social" style="left:431px;background:var(--social-a)" aria-label="Share">
    <svg width="10" height="10" viewBox="0 0 10 10"><circle cx="2" cy="5" r="1.5" fill="#fff"/><circle cx="8" cy="2" r="1.5" fill="#fff"/><circle cx="8" cy="8" r="1.5" fill="#fff"/><path d="M2 5L8 2M2 5l6 3" stroke="#fff" stroke-width="1"/></svg>
  </a>
  <a class="abs social" style="left:456px;background:var(--social-b)" aria-label="Link">
    <svg width="10" height="10" viewBox="0 0 10 10"><rect x="0.8" y="3" width="5" height="4" rx="2" fill="none" stroke="#fff" stroke-width="1.2"/><rect x="4.2" y="3" width="5" height="4" rx="2" fill="none" stroke="#fff" stroke-width="1.2"/></svg>
  </a>
  <a class="abs social" style="left:482px;background:var(--social-c)" aria-label="Email">
    <svg width="10" height="8" viewBox="0 0 10 8"><rect x="0.5" y="0.5" width="9" height="7" fill="none" stroke="#fff" stroke-width="1"/><path d="M0.5 1l4.5 3.5L9.5 1" fill="none" stroke="#fff" stroke-width="1"/></svg>
  </a>
</footer>

</body>
</html>
```